Veldmark Supplies Business Card

Professional business card that stand out to our potential customers. Front and back with clean modern design

Industry/Entity Type

Oil and gas

Contact Information for Business Card

Name, address, website , office phone and cell number

Requirements
Must have
• Editable files for each employee

```html
<!DOCTYPE html>
<html lang="en">
<head>
<meta charset="utf-8">
<title>Veldmark Supplies — Business Card</title>
<link rel="stylesheet" href="https://fonts.googleapis.com/css2?family=Poppins:wght@300;400;600;700&display=swap">
<style>
  :root {
    --page: #e3e6e7;
    --card: #202125;
    --red: #e8262b;
    --cyan: #14b0d3;
    --ink: #ecedee;
    --silver: #8a8c90;
  }
  * { box-sizing: border-box; margin: 0; padding: 0; }
  html, body {
    width: 1200px; height: 960px; overflow: hidden;
    background: var(--page);
    font-family: "Poppins", sans-serif;
  }
  .card {
    position: absolute; left: 249px; width: 702px; height: 400px;
    border-radius: 28px; overflow: hidden; background: var(--card);
  }
  .card--front { top: 60px; }
  .card--back { top: 500px; }

  .front-pattern {
    position: absolute; inset: 0;
    background:
      radial-gradient(ellipse 75% 70% at 100% 0%, rgba(235,236,238,0.55) 0%, rgba(140,142,146,0.25) 45%, rgba(32,33,37,0) 75%),
      linear-gradient(180deg, #25262a 0%, #1c1d20 100%);
  }
  .wordmark {
    position: absolute; display: flex; align-items: center; gap: 10px;
    font-weight: 700; color: var(--ink); white-space: nowrap;
    text-transform: uppercase; letter-spacing: 0.04em;
  }
  .wordmark__mark { width: 16px; height: 16px; background: var(--red); flex: none; }
  .card--front .wordmark { left: 50%; top: 175px; transform: translateX(-50%); font-size: 34px; }
  .card--front .wordmark__mark { width: 22px; height: 22px; }
  .card--back .wordmark { left: 150px; top: 186px; transform: translateX(-50%); font-size: 24px; }

  .divider {
    position: absolute; left: 350px; top: 85px; width: 1px; height: 228px;
    background: var(--red); opacity: 0.8;
  }
  .person { position: absolute; left: 398px; top: 110px; }
  .person__name { font-size: 33px; line-height: 1; color: var(--red); white-space: nowrap; }
  .person__first { font-weight: 700; }
  .person__last { font-weight: 300; }
  .person__title { margin-top: 9px; font-size: 18px; font-weight: 400; color: var(--cyan); }

  .contacts { position: absolute; left: 398px; top: 190px; list-style: none; }
  .contacts li {
    display: flex; align-items: center; gap: 12px; height: 24px;
    font-size: 18px; font-weight: 300; color: var(--ink); white-space: nowrap;
  }
  .contacts svg { width: 16px; height: 16px; flex: none; }

  .address {
    position: absolute; left: 0; right: 0; top: 355px; text-align: center;
    font-size: 17.5px; font-weight: 400; color: var(--cyan);
  }
</style>
</head>
<body>
  <section class="card card--front">
    <div class="front-pattern" role="img" aria-label="Repeating embossed monogram pattern fading to silver toward the top right"></div>
    <div class="wordmark"><span class="wordmark__mark"></span>Veldmark Supplies</div>
  </section>

  <section class="card card--back">
    <div class="wordmark"><span class="wordmark__mark"></span>Veldmark Supplies</div>
    <div class="divider"></div>

    <div class="person">
      <h1 class="person__name"><span class="person__first">Marisol</span> <span class="person__last">Okafor</span></h1>
      <p class="person__title">Co-Founder &amp; CEO</p>
    </div>

    <ul class="contacts">
      <li>
        <svg viewBox="0 0 16 16" aria-hidden="true"><path d="M3 1.5l2.4 0.2 1 3-1.5 1.2a8 8 0 0 0 5.2 5.2l1.2-1.5 3 1 0.2 2.4-1.8 1.5C7 14 2 9 1.5 3.3z" fill="var(--cyan)"/></svg>
        (432) 610-4185
      </li>
      <li>
        <svg viewBox="0 0 16 16" aria-hidden="true"><rect x="4" y="1" width="8" height="14" rx="1.5" fill="none" stroke="var(--red)" stroke-width="1.6"/></svg>
        (432) 775-3092
      </li>
      <li>
        <svg viewBox="0 0 16 16" aria-hidden="true"><circle cx="8" cy="8" r="7" fill="var(--cyan)"/><path d="M4 5c2 0 3 1 2.5 3S8 10 9 12M10 3c0 2 2 2 3 3" stroke="#ffffff" stroke-width="1.2" fill="none"/></svg>
        www.veldmarksupplies.com
      </li>
      <li>
        <svg viewBox="0 0 16 16" aria-hidden="true"><rect x="1" y="4" width="14" height="10" fill="var(--red)"/><path d="M1 4l7 6 7-6" fill="none" stroke="#ffffff" stroke-width="1.2"/></svg>
        hello@veldmarksupplies.com
      </li>
    </ul>

    <p class="address">1840 Mesa Ridge Rd. Suite 310 Odessa, TX 79761</p>
  </section>
</body>
</html>
```